Business Cards for new orthopaedic surgery practice

My husband and I are starting our own orthopaedic surgery practice. We are looking for a business card that is uniform, but one will have my name/title and the other will have his. You can just create one design with my name on it for now. But when I choose your design as the winning design I will ask that you add another copy with his name/title.

We are looking for classy, simple, elite all in one. We like dark blues/a little gold/yellow. Something that goes with our logo. We want our logo incorporated. Here is all the info you need:
Business name: RV Bone & Vitality Center
Location: 38517 North Willowmere Ave
Harbor Pines, FL 34219
Phone: 954-218-4063
Fax: 954-582-7341
Email: info@myrvbonecare.example

Names: Lydia Vance, M.D.
Board Certified Hand and Upper Extremity Surgeon

Ebo Dansu, M.D.
Board Certified Hip & Knee Replacement/General Orthopaedic Surgeon

Can decide what you want to put on the back. Maybe a slogan:
Steady in Care. Built Around You

I am just going to upload our logo. The only thing is if we select you as the winning design, the location, and phone numbers may change. We will need your help to update that once fully solidified.

Industry/Entity Type

Medical

Contact Information for Business Card

Colors
0054AA
0677BA
7BADD7
CADEEF
E8F1F8
0094D4
00A9DD
6FCCEA
C7EBF8
E9F6FB

Requirements
Must have
• class, appeal,
Should not have
• We want to air on the side of masculine if we are looking at masculine vs. feminine feel. But we still want it classy, sophisticated, and something we will love

```html
<!DOCTYPE html>
<html lang="en">
<head>
<meta charset="utf-8">
<title>RV Bone &amp; Vitality Center – Business Card</title>
<link rel="stylesheet" href="https://fonts.googleapis.com/css2?family=Cinzel:wght@600;700&family=Arimo:wght@400&display=swap">
<style>
  :root {
    --navy: #1f2f5a;
    --navy-deep: #1b2850;
    --navy-top: #263763;
    --gold: #c9a35c;
    --ink: #3a3a3a;
    --paper: #ffffff;
    --backdrop: #e6e6e6;
  }
  * { margin: 0; padding: 0; box-sizing: border-box; }
  html, body { width: 1200px; height: 1200px; overflow: hidden; }
  body { background: var(--backdrop); position: relative; font-family: "Arimo", Arial, sans-serif; }

  .card { position: absolute; width: 688px; height: 393px; overflow: hidden; }
  .card-front { left: 267px; top: 159px; background: var(--paper); }
  .card-back {
    left: 262px; top: 653px;
    background: linear-gradient(180deg, var(--navy-top) 0%, var(--navy-deep) 100%);
  }

  .person { position: absolute; left: 42px; top: 62px; }
  .person-name {
    font-family: "Cinzel", Georgia, serif; font-weight: 700;
    font-size: 22px; color: var(--navy); letter-spacing: 0.5px; line-height: 1;
  }
  .person-title {
    margin-top: 8px; font-size: 15px; line-height: 19px; color: var(--gold);
  }

  .address { position: absolute; left: 42px; top: 203px; font-size: 16px; line-height: 21px; color: var(--ink); font-style: normal; }

  .contacts { position: absolute; left: 42px; top: 258px; list-style: none; }
  .contacts li { display: flex; align-items: center; height: 20.5px; font-size: 16px; color: var(--ink); white-space: nowrap; }
  .contacts svg { width: 14px; height: 14px; margin-right: 11px; fill: #2a2a2a; flex: none; }

  .brand-seal {
    position: absolute; left: 333px; top: 43px; width: 308px; height: 308px;
    display: flex; align-items: center; justify-content: center;
  }
  .brand-seal .ring { position: absolute; inset: 0; }
  .brand-name {
    font-family: "Cinzel", Georgia, serif; font-weight: 700;
    font-size: 27px; line-height: 1.25; text-align: center; color: var(--navy);
    letter-spacing: 1px;
  }

  .back-brand {
    position: absolute; left: 0; right: 0; top: 146px;
    text-align: center;
    font-family: "Cinzel", Georgia, serif; font-weight: 700;
    font-size: 38px; line-height: 1.2; color: #ffffff; letter-spacing: 1px;
  }
  .slogan {
    position: absolute; left: 0; right: 0; top: 334px; text-align: center;
    font-size: 16px; letter-spacing: 3.2px; color: var(--gold); white-space: nowrap;
  }
</style>
</head>
<body>

<section class="card card-front" aria-label="Business card front">
  <div class="person">
    <h1 class="person-name">LYDIA VANCE, M.D.</h1>
    <p class="person-title">Board Certified Hand and<br>Upper Extremity Surgeon</p>
  </div>

  <address class="address">
    38517 North Willowmere Ave<br>Harbor Pines, FL 34219
  </address>

  <ul class="contacts">
    <li>
      <svg viewBox="0 0 24 24" aria-hidden="true"><path d="M6.6 10.8a15.1 15.1 0 0 0 6.6 6.6l2.2-2.2c.3-.3.7-.4 1-.2 1.1.4 2.3.6 3.6.6.6 0 1 .4 1 1V20c0 .6-.4 1-1 1A17 17 0 0 1 3 4c0-.6.4-1 1-1h3.5c.6 0 1 .4 1 1 0 1.3.2 2.5.6 3.6.1.3 0 .7-.2 1z"/></svg>
      954-218-4063
    </li>
    <li>
      <svg viewBox="0 0 24 24" aria-hidden="true"><path d="M6 2h12v5H6zM3 8h18a1 1 0 0 1 1 1v8h-4v5H6v-5H2V9a1 1 0 0 1 1-1zm5 8v4h8v-4z"/></svg>
      954-582-7341
    </li>
    <li>
      <svg viewBox="0 0 24 24" aria-hidden="true"><path d="M2 5h20v14H2zm2 2v.5l8 5 8-5V7zm0 3v7h16v-7l-8 5z"/></svg>
      info@myrvbonecare.example
    </li>
    <li>
      <svg viewBox="0 0 24 24" aria-hidden="true"><path d="M12 2a10 10 0 1 0 0 20 10 10 0 0 0 0-20zm-1 17.9A8 8 0 0 1 4.2 10L9 14.8v1a2 2 0 0 0 2 2zm6.9-2.5A2 2 0 0 0 16 16h-1v-3a1 1 0 0 0-1-1H8v-2h2a1 1 0 0 0 1-1V7h2a2 2 0 0 0 2-2v-.4a8 8 0 0 1 2.9 12.8z"/></svg>
      www.myrvbonecare.example
    </li>
  </ul>

  <div class="brand-seal">
    <svg class="ring" viewBox="0 0 308 308" aria-hidden="true">
      <circle cx="154" cy="154" r="150" fill="none" stroke="var(--gold)" stroke-width="3"/>
    </svg>
    <p class="brand-name">RV Bone &amp;<br>Vitality<br>Center</p>
  </div>
</section>

<section class="card card-back" aria-label="Business card back">
  <p class="back-brand">RV Bone &amp;<br>Vitality Center</p>
  <p class="slogan">STEADY IN CARE. BUILT AROUND YOU</p>
</section>

</body>
</html>
```